Web Design Project for Communications Agency

The design I need (PSD file) is for an agency offering specialised PR and communications services for customers in the healthcare sector.

OBJECTIVES OF THE WEBSITE:
1. To promote the agency's communication services
2. To position Solène Brivard as an industry leader, an expert in healthcare PR and communications by highlighting blogposts and social media.

WHAT I NEED:
1st, I need the design for the Home Page ONLY.
Once approved, I will need the other pages designed as well. (Here is prototype that we've already developed for the Website that will guide you in the design:
http://qorvelle.net/solenebrivard/)

VISUAL INSPIRATION
We want to give this Website a "Flat Design" look. Here are some websites for inspiration :
- http://tavrolinkworks.com/#!/process
- http://www.brindlemoss.co/
- http://quellaroft.com/

Also, reuse images found on the company's current Website :
http://www.solenebrivard.com/fr/index.html

HOMEPAGE MAIN ELEMENTS:
1. Main menu : 6 sections
Accueil | Agence | Services | Approche | Publications | Contact

2. Main Call To Action (big dark rectangle in prototype):
Can be slider or just an information bloc.

3. Publications récentes :
The 4 latest blog posts must be features on the homepage (will be linked with the "Publications" section)

4. Dynamic Footer :
Contains a Twitter feed and a Subscribe to our Newsletter feature (revecez nos publications)

OTHER PAGES (to design once Homepage is approved)
- Agence (about us)
- Services (our team)
- Approche (our approach)
- Publications (blog articles)
- Contact (Contact us)

Industry/Entity Type

Communications

Requirements
Must have
• Please refer to prototype :
http://qorvelle.net/solenebrivard/
Must have ALL features present in prototype.

Also, must reuse this picture in the design : http://solenebrivard.com/static/images/home-big-box.jpg

Finally, you will find attached the company logo.

```html
<!DOCTYPE html>
<html lang="fr">
<head>
<meta charset="utf-8">
<title>Solène Brivard – Cabinet-conseil</title>
<link href="https://fonts.googleapis.com/css2?family=Montserrat:wght@400;600;700&family=Open+Sans:wght@400;600&display=swap" rel="stylesheet">
<style>
:root{
  --brand-red:#c21c2b;
  --ink:#1e1e1e;
  --nav-ink:#222;
  --rule:#c9c9c9;
  --footer-bg:#333333;
  --footer-top:#5a5a5a;
  --footer-bottom:#2a2a2a;
  --footer-head:#f2f2f2;
  --footer-text:#9a9a9a;
  --footer-light:#d8d8d8;
  --caption-bg:rgba(30,30,30,.78);
  --white:#fff;
}
*{box-sizing:border-box;margin:0;padding:0}
html,body{width:818px;height:1200px;overflow:hidden}
body{position:relative;background:var(--white);font-family:'Montserrat',sans-serif;color:var(--ink)}

.site-header{position:absolute;top:0;left:0;width:818px;height:135px;background:var(--brand-red);display:flex;align-items:center;justify-content:center}
.brand-name{font-family:'Montserrat',sans-serif;font-weight:600;font-size:26px;line-height:28px;color:var(--white);text-align:left;width:120px;letter-spacing:.5px}

.main-nav{position:absolute;top:135px;left:0;width:818px;height:43px;display:flex;align-items:center}
.nav-links{display:flex;gap:0;list-style:none;margin-left:92px}
.nav-links li{font-size:8.5px;font-weight:400;color:var(--nav-ink);margin-right:23px;letter-spacing:.2px}
.social{position:absolute;left:603px;top:16px;display:flex;gap:9px}
.social span{width:11px;height:11px;border-radius:50%;background:#8a8a8a;display:block}
.lang-select{position:absolute;left:703px;top:13px;width:34px;height:18px;background:#dcdcdc;display:flex;align-items:center;justify-content:flex-end;padding-right:5px;font-size:6px;color:#333}
.lang-select i{position:absolute;left:6px;top:5px;width:14px;height:8px;background:#555;border-radius:2px}

.hero{position:absolute;top:178px;left:0;width:818px;height:292px;background:linear-gradient(100deg,#8d8d8d 0%,#c2c2c2 30%,#a8a8a8 55%,#6f6f6f 80%,#9a9a9a 100%);text-align:center}
.hero h1{position:absolute;top:93px;left:0;width:818px;font-weight:700;font-size:26.5px;line-height:34px;color:var(--white);text-shadow:0 1px 3px rgba(0,0,0,.35)}
.hero-cta{position:absolute;top:176px;left:326px;width:164px;height:34px;background:var(--brand-red);color:var(--white);font-weight:700;font-size:14px;line-height:34px;border-radius:2px}

.recent{position:absolute;top:495px;left:92px;width:635px}
.section-title{display:flex;align-items:center;gap:16px;font-weight:700;font-size:11px;height:20px}
.section-title::before,.section-title::after{content:"";flex:1;height:1px;background:var(--rule)}
.pub-grid{position:absolute;top:44px;left:0;display:grid;grid-template-columns:repeat(4,150px);grid-auto-rows:114px;column-gap:12px;row-gap:12.5px}
.pub-card{position:relative;overflow:hidden}
.pub-photo{position:absolute;inset:0}
.pub-title{position:absolute;left:0;bottom:0;width:100%;height:24px;background:var(--caption-bg);color:var(--white);font-size:9.2px;line-height:24px;text-align:center;font-weight:400}

.site-footer{position:absolute;top:927px;left:0;width:818px;height:273px;background:var(--footer-bg);border-top:6px solid var(--footer-top);font-family:'Open Sans',sans-serif}
.footer-col{position:absolute;top:35px}
.footer-col h3{font-family:'Montserrat',sans-serif;font-weight:600;font-size:9.5px;color:var(--footer-head);margin-bottom:17px}
.newsletter{left:95px;width:210px}
.newsletter p{font-size:8.6px;line-height:17px;color:var(--footer-text);padding-left:2px}
.subscribe-field{margin-top:8px;width:202px;height:26px;background:#4a4a4a;border-radius:2px;color:var(--footer-light);font-size:8.5px;line-height:26px;padding-left:12px}
.send-btn{margin-top:11px;width:42px;height:21px;background:#1a1a1a;color:var(--white);font-size:8.5px;line-height:21px;text-align:center;border-radius:2px}
.latest-posts{left:331px;width:192px}
.latest-posts ul{list-style:none}
.latest-posts li{font-size:7.6px;color:var(--footer-light);height:21px;line-height:20px;border-bottom:1px solid #4d4d4d;padding-left:10px;position:relative}
.latest-posts li:last-child{border-bottom:none}
.latest-posts li::before{content:"›";position:absolute;left:0;top:0;font-size:10px;color:var(--footer-light)}
.tweets{left:571px;width:170px}
.tweet{position:relative;padding-left:27px;font-size:8.8px;line-height:14px;color:var(--footer-light);margin-bottom:19px}
.tweet::before{content:"";position:absolute;left:1px;top:3px;width:14px;height:14px;border-radius:50%;background:#a5a5a5}
.tweet .msg{color:var(--footer-text)}
.footer-bar{position:absolute;top:1164px;left:0;width:818px;height:36px;background:var(--footer-bottom);font-family:'Open Sans',sans-serif;font-size:7.8px;color:var(--footer-light);line-height:36px;padding-left:95px}
</style>
</head>
<body>

<header class="site-header">
  <div class="brand-name">Solène Brivard</div>
</header>

<nav class="main-nav">
  <ul class="nav-links">
    <li>HOME</li><li>AGENCY</li><li>SERVICES</li><li>APPROACH</li><li>PUBLICATIONS</li><li>CONTACT</li>
  </ul>
  <div class="social" aria-label="Réseaux sociaux"><span></span><span></span><span></span><span></span></div>
  <div class="lang-select"><i></i>▾</div>
</nav>

<section class="hero">
  <div class="hero-photo" role="img" aria-label="Photo noir et blanc d'infirmières au travail" style="position:absolute;inset:0"></div>
  <h1>Cabinet-conseil en communications et affaires<br>spécialisé dans le secteur de la santé.</h1>
  <div class="hero-cta">EN SAVOIR PLUS</div>
</section>

<section class="recent">
  <h2 class="section-title">PUBLICATION RÉCENTES</h2>
  <div class="pub-grid">
    <article class="pub-card"><div class="pub-photo" role="img" aria-label="Médecin prenant la tension d'une patiente" style="background:linear-gradient(135deg,#e9eef0,#b9c4c9)"></div><div class="pub-title">TITRE DE LA PUBLICATION</div></article>
    <article class="pub-card"><div class="pub-photo" role="img" aria-label="Médecin à son bureau" style="background:linear-gradient(135deg,#f1f1f1,#cfd3d6)"></div><div class="pub-title">TITRE DE LA PUBLICATION</div></article>
    <article class="pub-card"><div class="pub-photo" role="img" aria-label="Médecin au chevet d'une patiente" style="background:linear-gradient(135deg,#d8cfc8,#8a7a70)"></div><div class="pub-title">TITRE DE LA PUBLICATION</div></article>
    <article class="pub-card"><div class="pub-photo" role="img" aria-label="Consultation entre médecin et patiente" style="background:linear-gradient(135deg,#e6eef2,#b5c3c9)"></div><div class="pub-title">TITRE DE LA PUBLICATION</div></article>
    <article class="pub-card"><div class="pub-photo" role="img" aria-label="Cube blanc orné d'une croix rouge" style="background:linear-gradient(135deg,#f4f4f4,#cfcfcf)"></div><div class="pub-title">TITRE DE LA PUBLICATION</div></article>
    <article class="pub-card"><div class="pub-photo" role="img" aria-label="Rangée de dominos" style="background:linear-gradient(135deg,#e2e2e2,#7d7d7d)"></div><div class="pub-title">TITRE DE LA PUBLICATION</div></article>
    <article class="pub-card"><div class="pub-photo" role="img" aria-label="Schéma manuscrit sur tableau blanc" style="background:linear-gradient(135deg,#f7f7f7,#dedede)"></div><div class="pub-title">TITRE DE LA PUBLICATION</div></article>
    <article class="pub-card"><div class="pub-photo" role="img" aria-label="Microphones de presse" style="background:linear-gradient(135deg,#f2f2f2,#9e9e9e)"></div><div class="pub-title">TITRE DE LA PUBLICATION</div></article>
    <article class="pub-card"><div class="pub-photo" role="img" aria-label="Médecin auscultant un patient" style="background:linear-gradient(135deg,#e8e4df,#a99a8c)"></div><div class="pub-title">TITRE DE LA PUBLICATION</div></article>
    <article class="pub-card"><div class="pub-photo" role="img" aria-label="Médecin examinant un enfant" style="background:linear-gradient(135deg,#cfdce8,#8c9eb0)"></div><div class="pub-title">TITRE DE LA PUBLICATION</div></article>
    <article class="pub-card"><div class="pub-photo" role="img" aria-label="Soignante avec une personne âgée" style="background:linear-gradient(135deg,#dcdad7,#8e8a86)"></div><div class="pub-title">TITRE DE LA PUBLICATION</div></article>
    <article class="pub-card"><div class="pub-photo" role="img" aria-label="Médecin au chevet d'une patiente" style="background:linear-gradient(135deg,#d8cfc8,#8a7a70)"></div><div class="pub-title">TITRE DE LA PUBLICATION</div></article>
  </div>
</section>

<footer class="site-footer">
  <div class="footer-col newsletter">
    <h3>SUBSCRIBE TO NEWSLETTER</h3>
    <p>Lorem Ipsum is simply dummy text of the printing and typesetting industry. Lorem Ipsum has been the industry's standard dummy text ever since the 1500s, when an unknown printer took a</p>
    <div class="subscribe-field">Subscribe</div>
    <div class="send-btn">Send</div>
  </div>
  <div class="footer-col latest-posts">
    <h3>LATEST POSTS</h3>
    <ul>
      <li>Lorem Ipsum Dolor Sit Amet and TypeSetting</li>
      <li>Lorem Ipsum Dolor Sit Amet and TypeSetting</li>
      <li>Lorem Ipsum Dolor Sit Amet and TypeSetting</li>
      <li>Lorem Ipsum Dolor Sit Amet and TypeSetting</li>
      <li>Lorem Ipsum Dolor Sit Amet and TypeSetting</li>
      <li>Lorem Ipsum Dolor Sit Amet and TypeSetting</li>
    </ul>
  </div>
  <div class="footer-col tweets">
    <h3>RECENT TWEETS</h3>
    <div class="tweet">@ Plume Atelier <span class="msg">new illustration for “Velmora”</span><br>5 days ago</div>
    <div class="tweet">@ Plume Atelier <span class="msg">logo for new Velmora intertainments</span><br>12 days ago</div>
    <div class="tweet">@ Atelier Nord <span class="msg">new design logo</span><br>12 days ago</div>
  </div>
</footer>

<div class="footer-bar">(c) Solène Brivard. Tous droits réservés.</div>

</body>
</html>
```